TA BRAMLEY BUSINESS CARD DESIGN PROJECT

We need to utilize our logo that was expertly created on PixelHarbor and now need to match this with a business card design.

```html
<!DOCTYPE html>
<html lang="en">
<head>
<meta charset="UTF-8">
<title>TA BRAMLEY Business Card</title>
<link href="https://fonts.googleapis.com/css2?family=Montserrat:wght@400;500;700&display=swap" rel="stylesheet">
<style>
  :root {
    --brand-blue: #0e55a9;
    --ink: #2b2b2b;
    --card-white: #ffffff;
    --backdrop: #e6dfd3;
  }
  * { margin: 0; padding: 0; box-sizing: border-box; }
  html, body {
    width: 1200px;
    height: 900px;
    overflow: hidden;
    background: var(--backdrop);
    font-family: "Montserrat", sans-serif;
  }
  .canvas {
    position: relative;
    width: 1200px;
    height: 900px;
  }
  .card {
    position: absolute;
    left: 310px;
    width: 582px;
    height: 332px;
    border-radius: 28px;
  }
  .card--front {
    top: 86px;
    background: var(--card-white);
  }
  .card--back {
    top: 470px;
    background: var(--brand-blue);
    display: flex;
    align-items: center;
    justify-content: center;
  }
  .identity {
    position: absolute;
    right: 317px;
    top: 142px;
    text-align: right;
  }
  .identity__name {
    color: var(--brand-blue);
    font-weight: 700;
    font-size: 20px;
    letter-spacing: 0.3px;
    line-height: 1.1;
  }
  .identity__role {
    color: var(--ink);
    font-weight: 400;
    font-size: 15px;
    line-height: 1.35;
  }
  .divider {
    position: absolute;
    left: 283px;
    top: 114px;
    width: 2px;
    height: 104px;
    background: var(--brand-blue);
  }
  .contact {
    position: absolute;
    left: 301px;
    top: 110px;
    color: var(--ink);
    font-size: 15px;
    line-height: 20px;
    list-style: none;
  }
  .contact__address { margin-bottom: 9px; }
  .contact__item {
    display: flex;
    align-items: center;
    gap: 6px;
  }
  .contact__icon {
    width: 13px;
    height: 13px;
    fill: var(--brand-blue);
    flex: none;
  }
  .wordmark {
    color: var(--card-white);
    font-weight: 700;
    font-size: 54px;
    letter-spacing: 6px;
  }
</style>
</head>
<body>
<main class="canvas">
  <section class="card card--front">
    <div class="identity">
      <p class="identity__name">OWEN HARTLEY</p>
      <p class="identity__role">Managing Director</p>
    </div>
    <div class="divider"></div>
    <ul class="contact">
      <li class="contact__address">Your address, City<br>State, Zip 1234</li>
      <li class="contact__item">
        <svg class="contact__icon" viewBox="0 0 16 16"><path d="M2 6c0-2 2-3 6-3s6 1 6 3v1h-3V5.5H5V7H2z M4 8h8l2 6H2z"/></svg>
        123 456 789
      </li>
      <li class="contact__item">
        <svg class="contact__icon" viewBox="0 0 16 16"><path d="M1 4h14v1L8 9 1 5z M1 6.5l7 4 7-4V13H1z"/></svg>
        info@yourmail.com
      </li>
      <li class="contact__item">
        <svg class="contact__icon" viewBox="0 0 16 16"><circle cx="8" cy="8" r="7"/><path d="M4 4l3 1 1 3-2 1-1 3-2-3z M10 3l3 2-1 3-2-1z" fill="#fff"/></svg>
        www.yourwebsite.com
      </li>
    </ul>
  </section>
  <section class="card card--back">
    <p class="wordmark">TA BRAMLEY</p>
  </section>
</main>
</body>
</html>
```